Venture Capital Investment Firm

We are looking to overhaul our existing website (substantially), with only using the same logos (which we can provide).
We are an investment firm that focuses on making loans to late stage technology companies. Our site should ultimately look like other venture capital firms, and look modern and fresh. We have an existing website www.norvellhub.com which this will be replacing, although we will be using a lot of the existing written content, and potentially the numbers of pages we will need, we are not wed to anything else. Please feel free to shoot any questions at any time and thank you in advance for your help!
Websites we like as examples:
https://www.tesmarkfund.com/
https://www.brindlewoodpartners.com/
Target Market(s)
Potential investors who will invest in our firm, as well as potentially companies that are looking to borrow money from us.
Coding
Coded - Design and coding required
Number of Pages Required
5+ page
Colors
Designer to choose colors to be used in the design.
Look and feel

```html
<!DOCTYPE html>
<html lang="en">
<head>
<meta charset="utf-8">
<title>Norvell Hub — Investment Partners</title>
<link rel="stylesheet" href="https://fonts.googleapis.com/css2?family=Cinzel:wght@700&family=Open+Sans:ital,wght@0,400;0,600;0,700;1,400&display=swap">
<style>
:root{
  --navy:#0b0a3a;
  --navy-soft:#3a3c66;
  --ink:#222;
  --text:#444;
  --muted:#777;
  --white:#fff;
  --footer:#121212;
  --footer-text:#d8d8d8;
}
*{margin:0;padding:0;box-sizing:border-box}
html,body{width:1200px;height:3766px;overflow:hidden}
body{position:relative;background:var(--white);font-family:"Open Sans",Arial,sans-serif;color:var(--text)}
.abs{position:absolute}
.heading{font-family:"Cinzel",Georgia,serif;font-weight:700;color:var(--navy);font-variant:small-caps}

/* header */
.brand{left:90px;top:52px;display:flex;align-items:center;gap:14px}
.brand-mark{width:40px;height:40px;border-radius:50%;background:var(--navy)}
.brand-name{font-family:"Cinzel",Georgia,serif;font-weight:700;font-size:36px;color:var(--navy);line-height:1}
.brand-sub{font-size:11px;font-weight:700;color:var(--navy);letter-spacing:.3px;margin-top:4px}
.topline{top:18px;right:91px;display:flex;gap:34px;align-items:center;font-size:19px;color:var(--ink)}
.topline .item{display:flex;align-items:center;gap:14px}
.topline .phone{font-weight:700}
.topline .mail{font-size:18px}
.ico-circle{width:44px;height:44px;border-radius:50%;border:2px solid var(--ink);display:flex;align-items:center;justify-content:center}
.nav{top:80px;right:92px;display:flex;gap:26px;font-size:16px;font-weight:700;color:var(--ink)}
.nav a{color:inherit;text-decoration:none}

/* hero */
.hero-svg{left:0;top:0}
.hero-title{left:0;width:1200px;top:400px;text-align:center;font-family:"Cinzel",Georgia,serif;font-weight:700;font-size:104px;color:var(--white);text-shadow:0 3px 8px rgba(0,0,0,.35);line-height:1}
.hero-sub{left:80px;width:1040px;top:516px;text-align:center;font-size:31px;line-height:40px;color:var(--white)}
.btn{display:flex;align-items:center;justify-content:center;gap:10px;border-radius:30px;font-weight:700;font-size:18px}
.btn-hero{left:504px;top:638px;width:190px;height:50px;background:var(--navy);color:var(--white);border:2px solid var(--white)}
.dots{left:563px;top:741px;display:flex;gap:14px}
.dots span{width:15px;height:15px;border-radius:50%;border:2px solid var(--white)}
.dots span.on{background:var(--white)}

/* about */
.about-art{left:94px;top:988px;width:412px;height:474px;border-radius:6px;background:linear-gradient(135deg,#8f8fa8 0%,#b5b4c8 45%,#6c6e8a 100%)}
.about-title{left:586px;top:1034px;font-size:48px}
.about-text{left:586px;top:1107px;width:524px;font-size:16.5px;line-height:34px;text-align:justify;color:var(--text)}
.btn-outline{left:586px;top:1373px;width:166px;height:52px;border:2px solid var(--navy);color:var(--navy);background:var(--white)}

/* strategy */
.strategy-title{left:0;width:1200px;top:1664px;text-align:center;font-size:48px;color:var(--white)}
.card{top:1757px;width:487px;height:184px;background:var(--white);border-radius:92px;display:flex;align-items:center}
.card-left{left:90px;padding-left:20px}
.card-right{left:621px;flex-direction:row-reverse;padding-right:20px}
.card-badge{width:146px;height:146px;border-radius:50%;border:18px solid var(--navy);display:flex;align-items:center;justify-content:center;flex-shrink:0}
.card-body{padding:0 24px 0 30px}
.card-right .card-body{padding:0 14px 0 18px}
.card-body h3{font-size:23px;font-weight:600;color:var(--ink);margin-bottom:12px}
.card-right .card-body h3{text-align:center}
.card-body p{font-size:16.5px;line-height:27px;color:#666}
.card-right .card-body p{text-align:center;font-size:16px}
.card-body p a{color:var(--navy);text-decoration:none}

/* team */
.team-title{left:0;width:1200px;top:2226px;text-align:center;font-size:50px}
.member{top:2323px;width:320px;text-align:center}
.member .portrait{width:320px;height:320px;border-radius:50%;background:radial-gradient(circle at 50% 40%,#6d6d78 0%,#2a2a3a 45%,var(--navy) 75%)}
.member .name{margin-top:58px;font-size:22px;color:var(--ink)}
.member .role{font-size:13.5px;font-style:italic;color:var(--muted);letter-spacing:.4px;margin-top:4px}
.member .links{display:flex;justify-content:center;gap:14px;margin-top:14px}
.member .links span{width:14px;height:12px;background:#777;border-radius:2px}

/* map */
.map{left:0;top:2901px;width:1200px;height:560px;background:linear-gradient(160deg,#d7e8cf 0%,#eeeae2 35%,#f2efe8 60%,#c9dff0 100%)}

/* footer */
.footer-svg{left:0;top:3150px}
.fcol{top:3500px;color:var(--footer-text);font-size:12.5px}
.fcol h4{font-size:16px;font-weight:600;color:var(--white);margin-bottom:16px;letter-spacing:.3px}
.fcol p{line-height:20px}
.fcol .row{display:flex;align-items:center;gap:16px;margin-top:14px;font-size:16px}
.links-grid{display:grid;grid-template-columns:133px 100px;row-gap:12px;font-size:12.5px}
.news-input{margin-top:18px;width:280px;height:40px;border:1px solid #444;display:flex}
.news-input span{flex:1;padding:12px 12px;font-size:11.5px;color:#ddd}
.news-input b{width:83px;background:var(--navy);color:#fff;font-weight:400;font-size:16px;display:flex;align-items:center;justify-content:center}
.social li{list-style:none;display:flex;align-items:center;gap:14px;margin-bottom:12px}
.social i{width:10px;height:10px;border-radius:50%;background:#ddd;display:block}
.copyright{left:0;width:1200px;top:3713px;text-align:center;font-size:12.5px;color:var(--footer-text)}
</style>
</head>
<body>

<svg class="abs hero-svg" width="1200" height="920" viewBox="0 0 1200 920">
  <defs>
    <linearGradient id="heroPhoto" x1="0" y1="0" x2="1" y2="1">
      <stop offset="0" stop-color="#2c3550"/>
      <stop offset=".45" stop-color="#8a93a6"/>
      <stop offset="1" stop-color="#c9ccd4"/>
    </linearGradient>
  </defs>
  <path d="M0 278 Q600 -16 1200 270 L1200 745 Q600 1030 0 790 Z" fill="var(--navy)"/>
  <path role="img" aria-label="Photo of business people reviewing documents at a meeting table" d="M0 300 Q600 -3 1200 350 L1200 730 Q600 1000 0 772 Z" fill="url(#heroPhoto)"/>
</svg>

<header>
  <div class="abs brand">
    <span class="brand-mark"></span>
    <div>
      <div class="brand-name">Norvell Hub</div>
      <div class="brand-sub">INVESTMENT PARTNERS, LLC</div>
    </div>
  </div>
  <div class="abs topline">
    <div class="item">
      <span class="ico-circle"><svg width="20" height="20" viewBox="0 0 24 24"><path d="M6.6 10.8a15 15 0 0 0 6.6 6.6l2.2-2.2c.3-.3.7-.4 1-.2 1.1.4 2.3.6 3.6.6.6 0 1 .4 1 1V20c0 .6-.4 1-1 1A17 17 0 0 1 3 4c0-.6.4-1 1-1h3.5c.6 0 1 .4 1 1 0 1.3.2 2.5.6 3.6.1.3 0 .7-.2 1z" fill="var(--ink)"/></svg></span>
      <span class="phone">+ 8 888 888 888</span>
    </div>
    <div class="item">
      <span class="ico-circle"><svg width="20" height="16" viewBox="0 0 20 16"><rect x="0" y="0" width="20" height="16" rx="2" fill="var(--ink)"/><path d="M1 2l9 7 9-7" stroke="#fff" stroke-width="1.6" fill="none"/></svg></span>
      <span class="mail">inquiries@norvellhub.com</span>
    </div>
  </div>
  <nav class="abs nav">
    <a href="#">HOME</a><a href="#">STRATEGY</a><a href="#">ABOUT US</a><a href="#">TEAM</a><a href="#">NEWS</a><a href="#">CONTACT</a><a href="#">INVESTORS</a>
  </nav>
</header>

<section>
  <h1 class="abs hero-title">NORVELL HUB</h1>
  <p class="abs hero-sub">We Are A Global Structured Credit Investment Firm Focused On The Healthcare And Technology Industries</p>
  <a class="abs btn btn-hero">Read More <svg width="16" height="16" viewBox="0 0 16 16"><circle cx="8" cy="8" r="8" fill="#fff"/><path d="M6 4l4 4-4 4" stroke="var(--navy)" stroke-width="2" fill="none"/></svg></a>
  <div class="abs dots"><span class="on"></span><span></span><span></span></div>
</section>

<section>
  <div class="abs about-art" role="img" aria-label="Photo of coin stacks and a rising financial chart"></div>
  <h2 class="abs heading about-title">About Us</h2>
  <p class="abs about-text">Norvell Hub is a private investment firm unique in its dual focus on life science and technology credit opportunities. Our ambidextrous approach to investing reflects a broad recognition and appreciation for the critical role intellectual property plays in the successful commercialization of products. We apply our extensive industry expertise to assess the revenue visibility created by these assets and offer a range of creative financing solutions.</p>
  <a class="abs btn btn-outline">Read More <svg width="16" height="16" viewBox="0 0 16 16"><circle cx="8" cy="8" r="8" fill="var(--navy)"/><path d="M6 4l4 4-4 4" stroke="#fff" stroke-width="2" fill="none"/></svg></a>
</section>

<svg class="abs" style="left:0;top:1480px" width="1200" height="680" viewBox="0 1480 1200 680">
  <defs>
    <linearGradient id="stratPhoto" x1="0" y1="0" x2="1" y2="1">
      <stop offset="0" stop-color="#56607e"/>
      <stop offset=".5" stop-color="#8b93ab"/>
      <stop offset="1" stop-color="#4a5272"/>
    </linearGradient>
  </defs>
  <path d="M0 1652 Q600 1385 1200 1630 L1200 1988 Q600 2250 0 2024 Z" fill="var(--navy)"/>
  <path role="img" aria-label="Photo of a city skyline and hands reviewing financial charts" d="M0 1673 Q600 1410 1200 1666 L1200 1973 Q600 2230 0 2002 Z" fill="url(#stratPhoto)"/>
</svg>

<section>
  <h2 class="abs heading strategy-title">Strategy</h2>
  <div class="abs card card-left">
    <div class="card-badge">
      <svg width="64" height="64" viewBox="0 0 64 64" fill="none" stroke="var(--navy)" stroke-width="2.5"><circle cx="32" cy="32" r="22"/><circle cx="32" cy="32" r="13"/><circle cx="32" cy="32" r="4" fill="var(--navy)"/><path d="M32 2v14M32 48v14M2 32h14M48 32h14"/></svg>
    </div>
    <div class="card-body">
      <h3>INDUSTRY FOCUS</h3>
      <p>Our focus spans the life science and technology industries, two sectors where ...<a>Read More</a></p>
    </div>
  </div>
  <div class="abs card card-right">
    <div class="card-badge">
      <svg width="62" height="54" viewBox="0 0 62 54" fill="none" stroke="var(--navy)" stroke-width="2.5"><rect x="8" y="14" width="46" height="28" rx="3"/><circle cx="31" cy="28" r="8"/><path d="M4 8h40l-5-5M58 48H18l5 5"/></svg>
    </div>
    <div class="card-body">
      <h3>TRANSACTION TYPES</h3>
      <p>Norvell Hub's proven strategy focuses on identifying opportunities where demonstrated ...<a>Read More</a></p>
    </div>
  </div>
</section>

<section>
  <h2 class="abs heading team-title">Our Team</h2>
  <div class="abs member" style="left:91px">
    <div class="portrait" role="img" aria-label="Black and white portrait of Elias Marlowe"></div>
    <div class="name">Elias Marlowe</div><div class="role">MANAGING PARTNER</div>
    <div class="links"><span></span><span></span></div>
  </div>
  <div class="abs member" style="left:441px">
    <div class="portrait" role="img" aria-label="Black and white portrait of Dev Ranganathan"></div>
    <div class="name">Dev Ranganathan</div><div class="role">MANAGING PARTNER</div>
    <div class="links"><span></span><span></span></div>
  </div>
  <div class="abs member" style="left:789px">
    <div class="portrait" role="img" aria-label="Black and white portrait of Owen Hartley"></div>
    <div class="name">Owen Hartley</div><div class="role">PARTNER</div>
    <div class="links"><span></span><span></span></div>
  </div>
</section>

<div class="abs map" role="img" aria-label="Street map showing the office location"></div>

<svg class="abs footer-svg" width="1200" height="616" viewBox="0 3150 1200 616">
  <path d="M0 3427 Q600 3150 1200 3464 L1200 3766 L0 3766 Z" fill="var(--navy)"/>
  <path d="M0 3464 Q600 3180 1200 3490 L1200 3766 L0 3766 Z" fill="var(--footer)"/>
</svg>

<footer>
  <div class="abs fcol" style="left:89px">
    <h4>CONTACT US</h4>
    <p>2150 Harlow Street #318<br>Bayview, CA &nbsp;94120</p>
    <div class="row"><svg width="18" height="18" viewBox="0 0 24 24"><path d="M6.6 10.8a15 15 0 0 0 6.6 6.6l2.2-2.2c.3-.3.7-.4 1-.2 1.1.4 2.3.6 3.6.6.6 0 1 .4 1 1V20c0 .6-.4 1-1 1A17 17 0 0 1 3 4c0-.6.4-1 1-1h3.5c.6 0 1 .4 1 1 0 1.3.2 2.5.6 3.6.1.3 0 .7-.2 1z" fill="none" stroke="#ddd" stroke-width="1.4"/></svg><span>+ 8 888 888 888</span></div>
    <div class="row" style="font-size:13.5px;margin-top:10px"><svg width="18" height="14" viewBox="0 0 18 14"><rect x=".7" y=".7" width="16.6" height="12.6" fill="none" stroke="#ddd" stroke-width="1.2"/><path d="M1 1l8 6 8-6" fill="none" stroke="#ddd" stroke-width="1.2"/></svg><span>inquiries@norvellhub.com</span></div>
  </div>
  <div class="abs fcol" style="left:370px">
    <h4>QUICK LINKS</h4>
    <div class="links-grid"><span>Home</span><span>News</span><span>Strategy</span><span>Contact</span><span>About Us</span><span>Investors</span><span>Team</span></div>
  </div>
  <div class="abs fcol" style="left:651px">
    <h4>NEWSLETTER</h4>
    <p style="width:250px">Excepteur sint occaecat cupidatat non proident, sunt in culpa qui</p>
    <div class="news-input"><span>Enter your email address</span><b>Sign Up</b></div>
  </div>
  <div class="abs fcol" style="left:995px">
    <h4>SOCIAL MEDIA</h4>
    <ul class="social"><li><i></i>Linkfold</li><li><i></i>Chirpline</li><li><i></i>Circlecast</li><li><i></i>Viewreel</li></ul>
  </div>
  <p class="abs copyright">© 2019.The Company Name.All Rights Reserved</p>
</footer>

</body>
</html>
```